K7 Electrical Services Ltd Web design

I require a web site for my new electrical contracting company. We are customer service orientated. Offering high value electrical installations, design and maintenance. Focused on custom residential and commercial upgrading. Lighting design and application are paramount in our company's services. Industry leading product use and integration are always on the forefront with our customer client services. As well as energy efficiency.

Target Market(s)

Homebuilders, General Contractors, Property management companies, clients, individuals,

Industry/Entity Type

Electric Company

Coding

Coded - Design and coding required

Number of Pages Required

3 page

Requirements
Must have
• Classic, modern, edgy but not trendy . Appeals to the masse.
• 3 page
• home page
• about page
• gallery page
• ability to contact from the webiste
Nice to have
• open to all types of designs that are relative to the construction industry.
• Black, Grey, metallic ice blue and deep purple colours from the logo.
Should not have
• anything cheesy with cartoon light bulb images.

```html
<!DOCTYPE html>
<html lang="en">
<head>
<meta charset="utf-8">
<title>K7 Electrical Services Ltd</title>
<link rel="stylesheet" href="https://fonts.googleapis.com/css2?family=Montserrat:ital,wght@0,400;0,500;0,600;0,700;0,800;1,800&family=Raleway:wght@400;500&display=swap">
<style>
:root{
  --purple:#6a2c91;
  --purple-bright:#8a3fc4;
  --navy:#0b1a33;
  --navy-deep:#050d1d;
  --grey-band:#e7e7e7;
  --ink:#333333;
  --muted:#7a7a7a;
  --white:#ffffff;
  --footer-dark:#2a2a2a;
  --heading:"Montserrat",Arial,sans-serif;
  --body:"Raleway",Arial,sans-serif;
}
*{box-sizing:border-box;margin:0;padding:0}
html,body{width:1200px;height:3046px;overflow:hidden;background:var(--white)}
body{position:relative;font-family:var(--body);color:var(--ink)}
.abs{position:absolute}

/* header */
.topbar{left:0;top:0;width:1200px;height:60px;background:var(--white)}
.menu-toggle{left:22px;top:20px;display:flex;align-items:center;gap:14px;font:500 14px var(--heading);color:var(--ink)}
.menu-toggle svg{display:block}
.helpline{left:536px;top:16px;display:flex;align-items:center;gap:8px;font:500 14px var(--heading);color:var(--ink)}
.helpline strong{font:500 22px var(--heading);color:var(--purple);margin-left:4px}
.nav-projects{left:880px;top:22px;font:500 13px var(--heading);letter-spacing:1.5px;color:var(--ink)}
.quote-btn{left:1003px;top:0;width:197px;height:60px;background:var(--purple);color:var(--white);font:600 14px var(--heading);letter-spacing:1px;display:flex;align-items:center;justify-content:center}

/* side tabs */
.side-tab{left:0;width:60px;display:flex;align-items:center;justify-content:center}
.side-tab span{display:block;width:12px;font:500 12px var(--heading);letter-spacing:0;text-align:center;line-height:20px;word-break:break-all}
.tab-commercial{top:60px;height:255px;background:var(--white);border-right:1px solid #ddd}
.tab-commercial span{color:var(--purple)}
.tab-residential{top:315px;height:278px;background:var(--purple)}
.tab-residential span{color:var(--white)}

/* hero */
.hero{left:60px;top:60px;width:1140px;height:533px;background:
  radial-gradient(ellipse 520px 220px at 620px 190px,rgba(60,140,220,.45),transparent 70%),
  radial-gradient(ellipse 700px 300px at 300px 420px,rgba(30,80,160,.35),transparent 70%),
  linear-gradient(160deg,#0e2142 0%,var(--navy) 45%,var(--navy-deep) 100%)}
.hero-photo{left:690px;top:60px;width:380px;height:460px;background:linear-gradient(180deg,rgba(150,160,175,.55),rgba(35,75,170,.85) 45%,rgba(30,60,140,.9));border-radius:180px 180px 0 0}
.brand-mark{left:130px;top:140px;display:flex;flex-direction:column;align-items:flex-start}
.brand-mark .brand-name{font:700 30px/1.1 var(--heading);color:var(--white);letter-spacing:1px}
.hero-kicker{left:130px;top:284px;font:500 19px var(--heading);color:var(--white)}
.hero-title{left:130px;top:308px;font:italic 800 40px var(--heading);color:var(--purple-bright);letter-spacing:.5px}
.hero-copy{left:130px;top:362px;width:480px;font:500 13px/24px var(--heading);color:var(--white)}
.btn-solid{height:33px;display:flex;align-items:center;justify-content:center;font:600 11px var(--heading);letter-spacing:.8px;color:var(--white)}
.btn-company{left:130px;top:427px;width:120px;background:var(--purple)}
.btn-contact{left:258px;top:427px;width:120px;background:#3b3b3b}

/* about */
.about-photo{left:642px;top:516px;width:558px;height:416px;background:linear-gradient(135deg,#c7b9a7 0%,#8a7f74 40%,#2b2b30 70%,#6c5a4a 100%)}
.eyebrow{font:500 13px var(--heading);letter-spacing:1px;color:var(--ink)}
.section-title{font:600 28px var(--heading);letter-spacing:1.5px;color:var(--purple)}
.body-copy{font:400 13.5px/24px var(--body);color:var(--muted);letter-spacing:.3px}
.btn-outline{height:35px;border:1.5px solid var(--purple);display:flex;align-items:center;justify-content:center;font:500 13px var(--heading);letter-spacing:1.5px;color:var(--purple)}
.about-eyebrow{left:132px;top:634px}
.about-title{left:130px;top:654px}
.about-copy{left:126px;top:710px;width:410px}
.about-btn{left:124px;top:867px;width:181px;background:var(--white)}

/* why choose us */
.why-band{left:0;top:989px;width:1200px;height:406px;background:var(--grey-band)}
.why-photo{left:0;top:1060px;width:557px;height:432px;background:linear-gradient(120deg,#3a4a45 0%,#6d7a72 35%,#d6c9a0 55%,#b8c5d2 80%,#7d8a96 100%)}
.why-eyebrow{left:609px;top:1052px}
.why-title{left:609px;top:1074px}
.why-copy{left:615px;top:1131px;width:410px}
.why-btn{left:611px;top:1285px;width:181px;background:transparent}
.benefit{top:1418px;width:140px;display:flex;flex-direction:column;align-items:center;gap:10px;font:600 12px var(--heading);letter-spacing:1px;color:var(--ink)}
.benefit-time{left:612px}
.benefit-effort{left:791px}
.benefit-money{left:976px}

/* projects */
.projects-block{left:0;top:1570px;width:481px;height:363px;background:var(--purple)}
.projects-eyebrow{left:132px;top:1624px;font:500 13px var(--heading);letter-spacing:1px;color:var(--white)}
.projects-title{left:130px;top:1654px;font:600 28px var(--heading);letter-spacing:1.5px;color:var(--white)}
.project{background:#555}
.project-a{left:61px;top:1728px;width:526px;height:363px;background:linear-gradient(135deg,#5a7c9a,#30485e 50%,#8c6a5a)}
.project-a .frame{position:absolute;left:16px;top:10px;right:16px;bottom:10px;border:1.5px solid rgba(255,255,255,.85)}
.project-a .caption{position:absolute;left:0;right:0;top:162px;text-align:center;font:600 16px var(--heading);letter-spacing:1px;color:var(--white)}
.project-a .zoom{position:absolute;left:253px;top:196px}
.project-b{left:611px;top:1728px;width:528px;height:363px;background:linear-gradient(135deg,#c9c2b3,#8e8577 40%,#2e4a86 75%,#3c5a9c)}
.project-c{left:61px;top:2116px;width:345px;height:363px;background:linear-gradient(160deg,#b7b2aa,#7e756c 40%,#2c2f45 70%,#5a4630)}
.project-d{left:426px;top:2116px;width:345px;height:363px;background:linear-gradient(160deg,#8d8f93,#6e6f73 40%,#b28050 70%,#8f6a45)}
.project-e{left:794px;top:2116px;width:345px;height:363px;background:linear-gradient(160deg,#e6e6e6,#7b7f86 35%,#2a2a2e 65%,#6b4a3c)}

/* footer */
.footer{left:0;top:2577px;width:1200px;height:432px;background:var(--purple)}
.footer-brand{left:0;top:2628px;width:1200px;text-align:center;font:700 32px/1.1 var(--heading);color:var(--white);letter-spacing:1px}
.contact-col{top:2740px;width:300px;display:flex;flex-direction:column;align-items:center;color:var(--white);text-align:center}
.contact-col .icon-circle{width:46px;height:46px;border-radius:50%;background:#2f2f2f;display:flex;align-items:center;justify-content:center}
.contact-col h3{margin-top:20px;font:700 15px var(--heading);letter-spacing:.8px}
.contact-col p{margin-top:14px;font:400 12.5px/19px var(--heading)}
.col-address{left:116px}
.col-phone{left:437px}
.col-mail{left:764px}
.footer-nav{left:0;top:2926px;width:1200px;display:flex;justify-content:center;gap:42px;font:600 12px var(--heading);letter-spacing:.8px;color:var(--white)}
.footer-social{left:0;top:2966px;width:1200px;display:flex;justify-content:center;gap:14px}
.footer-social span{width:18px;height:18px;border-radius:50%;background:var(--white)}
.copyright{left:0;top:3009px;width:1200px;height:37px;background:var(--footer-dark);color:var(--white);font:400 12px var(--heading);display:flex;align-items:center;justify-content:center}
.copyright strong{font-weight:700;margin:0 3px}
</style>
</head>
<body>

<header class="abs topbar">
  <div class="abs menu-toggle">
    <svg width="20" height="14" viewBox="0 0 20 14"><rect y="0" width="20" height="2" fill="#333"/><rect y="6" width="14" height="2" fill="#333"/><rect y="12" width="20" height="2" fill="#333"/></svg>
    Menu
  </div>
  <div class="abs helpline">
    <svg width="22" height="22" viewBox="0 0 24 24"><path d="M6.6 10.8a15.1 15.1 0 0 0 6.6 6.6l2.2-2.2a1 1 0 0 1 1-.25 11.4 11.4 0 0 0 3.6.57 1 1 0 0 1 1 1V20a1 1 0 0 1-1 1A17 17 0 0 1 3 4a1 1 0 0 1 1-1h3.5a1 1 0 0 1 1 1c0 1.25.2 2.45.57 3.57a1 1 0 0 1-.25 1z" fill="#6a2c91"/></svg>
    Need Help? Call us: <strong>(555) 010-2040</strong>
  </div>
  <div class="abs nav-projects">OUR PROJECTS</div>
  <div class="abs quote-btn">GET A QUOTE</div>
</header>

<div class="abs side-tab tab-commercial"><span>COMMERCIAL</span></div>
<div class="abs side-tab tab-residential"><span>RESIDENTIAL</span></div>

<section class="abs hero" aria-label="Hero"></section>
<div class="abs hero-photo" role="img" aria-label="Smiling electrician in blue overalls carrying a coil of cable, holding a multimeter"></div>
<div class="abs brand-mark"><span class="brand-name">K7 ELECTRICAL<br>SERVICES</span></div>
<div class="abs hero-kicker">K7 Electrical Services</div>
<h1 class="abs hero-title">Fast Electrical Services!</h1>
<p class="abs hero-copy">Universal business theme continues to grow&nbsp; continues to grow ever day thanks to the confidence our clients have in US.</p>
<a class="abs btn-solid btn-company">OUR COMPANY</a>
<a class="abs btn-solid btn-contact">CONTACT US</a>

<div class="abs about-photo" role="img" aria-label="Electrician in a yellow hard hat giving a thumbs up beside an outdoor air conditioning unit"></div>
<div class="abs eyebrow about-eyebrow">ABOUT US</div>
<h2 class="abs section-title about-title">WHO WE ARE</h2>
<p class="abs body-copy about-copy">We know what works, what rents, and how to get more for your property. It is the Group's vision to remain the best service provider and property manager in Carvoeiro, Lagoa and surrounding areas and the top holiday destination in the Algarve with that something extra.</p>
<a class="abs btn-outline about-btn">READ MORE</a>

<section class="abs why-band" aria-label="Why choose us"></section>
<div class="abs why-photo" role="img" aria-label="Electrician in a yellow hard hat testing a fuse panel with a multimeter"></div>
<div class="abs eyebrow why-eyebrow">OUR SPECIALITIES</div>
<h2 class="abs section-title why-title">WHY CHOOSE US</h2>
<p class="abs body-copy why-copy">We know what works, what rents, and how to get more for your property. It is the Group's vision to remain the best service provider and property manager in Carvoeiro, Lagoa and surrounding areas and the top holiday destination in the Algarve with that something extra.</p>
<a class="abs btn-outline why-btn">READ MORE</a>

<div class="abs benefit benefit-time">
  <svg width="40" height="40" viewBox="0 0 40 40"><circle cx="20" cy="20" r="16" fill="none" stroke="#6a2c91" stroke-width="2.5"/><path d="M20 4a16 16 0 0 1 15 10" fill="none" stroke="#6a2c91" stroke-width="2.5"/><text x="20" y="25" text-anchor="middle" font-family="Montserrat, sans-serif" font-size="13" font-weight="700" fill="#333">24</text></svg>
  SAVE TIME
</div>
<div class="abs benefit benefit-effort">
  <svg width="40" height="40" viewBox="0 0 40 40"><path d="M10 30l8-8M16 16l8 8M20 12l8-8M28 20l8-8M14 14l12 12-6 6a6 6 0 0 1-8 0l-4-4a6 6 0 0 1 0-8z" fill="none" stroke="#6a2c91" stroke-width="2.5" stroke-linecap="round"/><path d="M6 34l4-4" stroke="#6a2c91" stroke-width="2.5" stroke-linecap="round"/></svg>
  SAVE EFFORT
</div>
<div class="abs benefit benefit-money">
  <svg width="40" height="40" viewBox="0 0 40 40"><rect x="4" y="10" width="32" height="20" rx="2" fill="none" stroke="#6a2c91" stroke-width="2.5"/><circle cx="20" cy="20" r="5" fill="#6a2c91"/><path d="M8 14h3M29 26h3" stroke="#6a2c91" stroke-width="2.5"/></svg>
  SAVE MONEY
</div>

<section class="abs projects-block" aria-label="Featured projects"></section>
<div class="abs projects-eyebrow">OUR RECENT PROJECTS</div>
<h2 class="abs projects-title">FEATURED PROJECTS</h2>

<div class="abs project project-a" role="img" aria-label="Hands working on wiring inside a residential distribution board">
  <div class="frame"></div>
  <div class="caption">RESIDENTIAL SOLUTION</div>
  <svg class="zoom" width="20" height="20" viewBox="0 0 20 20"><circle cx="8" cy="8" r="6" fill="none" stroke="#fff" stroke-width="1.8"/><path d="M12.5 12.5l5 5" stroke="#fff" stroke-width="1.8" stroke-linecap="round"/></svg>
</div>
<div class="abs project project-b" role="img" aria-label="Electrician in a blue hard hat and face shield wearing gloves, working on a panel"></div>
<div class="abs project project-c" role="img" aria-label="Electrician in a white hard hat with a tool belt wiring a wall-mounted panel"></div>
<div class="abs project project-d" role="img" aria-label="Electrician in a yellow hard hat and safety glasses connecting cables"></div>
<div class="abs project project-e" role="img" aria-label="Two workers in white hard hats fitting heavy cables in an industrial installation"></div>

<footer class="abs footer" aria-label="Footer"></footer>
<div class="abs footer-brand">K7 ELECTRICAL<br>SERVICES</div>

<div class="abs contact-col col-address">
  <div class="icon-circle"><svg width="20" height="20" viewBox="0 0 24 24"><path d="M12 2a7 7 0 0 0-7 7c0 5 7 13 7 13s7-8 7-13a7 7 0 0 0-7-7z" fill="none" stroke="#fff" stroke-width="1.8"/><circle cx="12" cy="9" r="2.5" fill="none" stroke="#fff" stroke-width="1.8"/></svg></div>
  <h3>ADDRESS</h3>
  <p>Northgate Studio Workshop<br>24-26 Harbour Road</p>
</div>
<div class="abs contact-col col-phone">
  <div class="icon-circle"><svg width="20" height="20" viewBox="0 0 24 24"><path d="M6.6 10.8a15.1 15.1 0 0 0 6.6 6.6l2.2-2.2a1 1 0 0 1 1-.25 11.4 11.4 0 0 0 3.6.57 1 1 0 0 1 1 1V20a1 1 0 0 1-1 1A17 17 0 0 1 3 4a1 1 0 0 1 1-1h3.5a1 1 0 0 1 1 1c0 1.25.2 2.45.57 3.57a1 1 0 0 1-.25 1z" fill="none" stroke="#fff" stroke-width="1.6"/></svg></div>
  <h3>PHONE</h3>
  <p>+ 03 5550 1234, + 03 5550 1234,<br>+ 03 5550 1234.</p>
</div>
<div class="abs contact-col col-mail">
  <div class="icon-circle"><svg width="20" height="20" viewBox="0 0 24 24"><rect x="3" y="6" width="18" height="13" rx="1" fill="none" stroke="#fff" stroke-width="1.8"/><path d="M3 7l9 7 9-7" fill="none" stroke="#fff" stroke-width="1.8"/></svg></div>
  <h3>ADDRESS</h3>
  <p>admin@k7electrical.example<br>info@k7electrical.example</p>
</div>

<nav class="abs footer-nav">
  <a>FEATURES</a><a>RESIDENTIAL</a><a>COMMERCIAL</a><a>REVIEWS</a><a>CONTACT US</a>
</nav>
<div class="abs footer-social" aria-label="Social links">
  <span></span><span></span><span></span><span></span>
</div>
<div class="abs copyright">Copyright © 2017 <strong>k7electrical.example</strong> All rights reserved.</div>

</body>
</html>
```